Meridian Crestline Motors *

Professional business cards for our auto wholesale dealership.

Target Market(s)

New and used cars sales managers and middle class to higher end private party buyers.

Industry/Entity Type

Automotive

Contact Information for Business Card

Meridian Crestline Motors
Darnell R Okonski
Owner
(555) 304-6618
mercrestmotors@quillbox.example
Dealer Lic # 48265

Logo Text

Meridian Crestline Motors, Mer Crest Motors, MCM, etc

Font styles to use
Serif
Sans Serif

Colors

Designer to choose colors to be used in the design.

Requirements
Must have
• A professional, but not pretentious, look
Nice to have
• It might be nice to see "MCM" in a shape form i.e. circle, triangle, etc in the corner or background somehwere
Should not have
• bright "girly" colors

```html
<!DOCTYPE html>
<html lang="en">
<head>
<meta charset="UTF-8">
<title>Meridian Crestline Motors — Business Card</title>
<link href="https://fonts.googleapis.com/css2?family=Open+Sans:wght@400;600&display=swap" rel="stylesheet">
<style>
  :root {
    --bg: #2a2a2a;
    --card-black: #0d0d0d;
    --card-white: #f1f1f0;
    --brand-red: #c3171d;
    --text-white: #f4f4f4;
  }
  * { margin: 0; padding: 0; box-sizing: border-box; }
  html, body {
    width: 1200px; height: 900px; overflow: hidden;
    background: var(--bg);
    font-family: "Open Sans", Arial, sans-serif;
  }
  .stage {
    position: relative; width: 1200px; height: 900px;
    display: flex; justify-content: center; align-items: center; gap: 80px;
  }
  .card {
    position: relative; width: 400px; height: 700px;
    background: var(--card-black); overflow: hidden;
    box-shadow: 0 20px 40px rgba(0,0,0,0.5);
  }
  .card-front__top {
    position: absolute; top: 0; left: 0; width: 400px; height: 420px;
  }
  .brand-mark {
    position: absolute; left: 0; right: 0;
    display: flex; flex-direction: column; align-items: center; gap: 12px;
  }
  .card-front .brand-mark { top: 60px; }
  .card-back .brand-mark { top: 140px; }
  .brand-mark__ring {
    width: 150px; height: 150px; border-radius: 50%;
    border: 14px solid var(--brand-red);
  }
  .brand-mark__name {
    color: var(--brand-red); font-weight: 600; font-size: 26px;
    text-align: center; line-height: 1.2; letter-spacing: 0.5px;
  }
  .contact {
    position: absolute; left: 0; right: 0; bottom: 60px;
    text-align: center;
  }
  .contact__name { color: var(--brand-red); font-weight: 600; font-size: 28px; line-height: 1.3; }
  .contact__role { color: var(--text-white); font-size: 19px; margin-top: 0; }
  .contact__phone {
    color: var(--brand-red); font-weight: 600; font-size: 28px;
    letter-spacing: 3px; margin-top: 40px;
  }
  .contact__line { color: var(--text-white); font-size: 18px; margin-top: 4px; }
</style>
</head>
<body>
<div class="stage">
  <section class="card card-front">
    <svg class="card-front__top" viewBox="0 0 400 420" aria-hidden="true">
      <path d="M0 0 H400 V215 Q310 415 0 392 Z" fill="var(--card-white)"/>
    </svg>
    <div class="brand-mark">
      <div class="brand-mark__ring"></div>
      <div class="brand-mark__name">Meridian Crestline<br>Motors</div>
    </div>
    <div class="contact">
      <div class="contact__name">Darnell R Okonski</div>
      <div class="contact__role">Owner</div>
      <div class="contact__phone">(555) 304-6618</div>
      <div class="contact__line">mercrestmotors@quillbox.example</div>
      <div class="contact__line">Dealer Lic # 48265</div>
    </div>
  </section>

  <section class="card card-back">
    <div class="brand-mark">
      <div class="brand-mark__ring"></div>
      <div class="brand-mark__name">Meridian Crestline<br>Motors</div>
    </div>
  </section>
</div>
</body>
</html>
```